KVR - Redesign (PSD Files Only)

Requirements for the site:

1. We need our logo recreated, please use the same design and change colors to work on a white background

2. The site is a "Wizard" based site, that takes the customer through the process of creating a unique web presence that suits there needs

3.Colors Needed - Main "Dark Blue" Secondary = "Dark Grey" -Other = "Light Grey and White"

4.We need a CRISP CLEAN DESIGN, simple design

5.Wireframes are a general layout and may be modified by you to enhance the design

6. We want a complete web 5.0 look with big buttons and text boxes

7.The more personality the better

8. Current Site brightpolehub.example

9.See attachments for wireframes

10. Designer should deliver PSD files, no coding is required

11. The portfolio wireframe, should look like the design of the artflockly portfolio template
Updates

KEEP IT SIMPLE.,.....

We like the quillmark scaffold style of designs

```html
<!DOCTYPE html>
<html lang="en">
<head>
<meta charset="utf-8">
<title>About Us – KVR Studios Inc</title>
<link href="https://fonts.googleapis.com/css2?family=Dosis:wght@500;600;700&family=Open+Sans:ital,wght@0,400;0,600;1,400&display=swap" rel="stylesheet">
<style>
  :root{
    --blue-deep:#08305c;
    --blue-mid:#0a4a86;
    --blue-glow:#0f6db0;
    --blue-line:#1c4f7e;
    --header-dark:#1b1b1b;
    --footer-dark:#222222;
    --footer-bar:#1a1a1a;
    --nav-active:#0d4a86;
    --orange-top:#ffa53a;
    --orange-bot:#ff7a00;
    --white:#ffffff;
  }
  *{margin:0;padding:0;box-sizing:border-box}
  html,body{width:1200px;height:1005px;overflow:hidden}
  body{position:relative;font-family:"Open Sans",sans-serif;color:var(--white);background:var(--footer-dark)}
  .main{position:absolute;left:0;top:0;width:1200px;height:772px;
    background:radial-gradient(ellipse 420px 260px at 720px 60px,var(--blue-glow) 0%,transparent 80%),
      linear-gradient(180deg,var(--blue-mid) 0%,var(--blue-deep) 55%,#0a3868 100%)}
  .topstrip{position:absolute;left:0;top:0;width:1200px;height:23px;background:#151515}
  .header-bar{position:absolute;left:129px;top:0;width:943px;height:46px;background:var(--header-dark)}
  .logo{position:absolute;left:18px;top:-40px;width:108px;height:134px;border-radius:0 0 54px 54px;
    background:var(--header-dark);display:flex;align-items:flex-end;justify-content:center;padding-bottom:28px}
  .logo-name{font-family:"Dosis",sans-serif;font-weight:700;font-size:30px;color:var(--white);line-height:1}
  .nav{position:absolute;left:170px;top:0;display:flex;height:46px}
  .nav a{font-family:"Dosis",sans-serif;font-weight:500;font-size:20px;color:var(--white);text-decoration:none;
    padding:0 13px;line-height:46px;white-space:nowrap}
  .nav a.active{background:var(--nav-active)}
  .social{display:flex;gap:7px}
  .social span{display:block;border-radius:50%;background:var(--white)}
  .header-social{position:absolute;left:575px;top:10px}
  .header-social span{width:26px;height:26px}
  .phone{display:flex;align-items:center;gap:6px;font-family:"Dosis",sans-serif;font-weight:500;color:var(--white);white-space:nowrap}
  .header-phone{position:absolute;left:756px;top:7px;font-size:27px;line-height:32px}
  .page-title{position:absolute;left:129px;top:118px;font-family:"Dosis",sans-serif;font-weight:700;font-size:38px}
  .title-rule{position:absolute;left:129px;top:172px;width:943px;height:2px;background:#0a2547;border-bottom:1px solid var(--blue-line)}
  .owner-photo{position:absolute;left:129px;top:203px;width:381px;height:271px;
    background:linear-gradient(135deg,#e9ecef 0%,#cfd4d8 55%,#8f8c88 100%)}
  .owner-name{position:absolute;left:528px;top:205px;font-size:27px;font-weight:600;letter-spacing:.3px}
  .owner-rule{position:absolute;left:528px;top:248px;width:543px;height:2px;background:var(--blue-line)}
  .owner-bio{position:absolute;left:528px;top:264px;width:545px;font-size:13.7px;line-height:17.2px}
  .btn{position:absolute;display:flex;align-items:center;justify-content:center;
    background:linear-gradient(180deg,var(--orange-top),var(--orange-bot));
    font-family:"Dosis",sans-serif;font-weight:700;font-size:27px;color:var(--white);text-decoration:none;white-space:nowrap}
  .btn-main{left:529px;top:474px;width:243px;height:55px}
  .btn-caption{position:absolute;left:531px;top:540px;font-size:16px;line-height:19px}
  .info-box{position:absolute;left:129px;top:659px;width:942px;height:52px;border:1px solid var(--blue-line);
    display:flex;align-items:center;padding-left:15px;gap:13px;font-style:italic;font-size:16px}
  .info-icon{width:28px;height:28px;border-radius:50%;background:radial-gradient(circle at 40% 35%,#e4e6e8,#8a9096);
    color:#1e2b3a;font-weight:600;font-family:Georgia,serif;font-size:18px;display:flex;align-items:center;justify-content:center}
  .footer-links{position:absolute;left:129px;top:815px;font-size:12.5px;line-height:19px}
  .footer-links a{color:var(--white);text-decoration:none}
  .footer-social{position:absolute;left:498px;top:811px}
  .footer-social span{width:38px;height:38px}
  .footer-phone{position:absolute;left:498px;top:854px;font-size:27px;line-height:32px}
  .btn-footer{left:828px;top:811px;width:243px;height:55px}
  .footer-bar{position:absolute;left:129px;top:897px;width:948px;height:53px;background:var(--footer-bar)}
  .partner-badge{position:absolute;left:0;top:0;width:157px;height:53px;background:#f3f3f3;border-left:54px solid #3b6fd4}
</style>
</head>
<body>
  <div class="main"></div>
  <div class="topstrip"></div>

  <header class="header-bar">
    <div class="logo"><span class="logo-name">KVR</span></div>
    <nav class="nav">
      <a href="#">Home</a>
      <a href="#" class="active">About Us</a>
      <a href="#">Portfolio</a>
      <a href="#">Contact Us</a>
    </nav>
    <div class="social header-social">
      <span aria-label="Social network"></span><span aria-label="Social network"></span>
      <span aria-label="Video channel"></span><span aria-label="Social network"></span>
    </div>
    <div class="phone header-phone">
      <svg width="14" height="20" viewBox="0 0 14 20"><path d="M3 1 L6 1 L7 6 L5 7.5 Q6.5 12 9 14 L10.5 12.5 L13.5 15 L12 19 Q2 16 1 4 Z" fill="#fff"/></svg>
      1800-555-0142
    </div>
  </header>

  <h1 class="page-title">About Our Owner</h1>
  <div class="title-rule"></div>

  <div class="owner-photo" role="img" aria-label="Photo of the owner seated at a desk with a desktop computer in a bright studio"></div>
  <h2 class="owner-name">CEO - MARCUS ELLERY</h2>
  <div class="owner-rule"></div>
  <p class="owner-bio">Lorem ipsum dolor sit amet, consectetur adipiscing elit. In fermentum dolor non augue pretium egestas. Donec sem eros, tincidunt at congue ut, posuere sit amet est. Vivamus scelerisque viverra odio sit amet laoreet. Ut nec neque non justo rutrum tempor lobortis eu ante. Aliquam sagittis, nibh quis commodo auctor, risus mauris laoreet lectus, id facilisis libero odio nec enim. Sed id ligula adipiscing purus lacinia aliquet. Sed eu est non nisl vehicula bibendum congue sit amet enim. Lorem ipsum dolor sit amet, consectetur adipiscing elit. In fermentum dolor non augue pretium egestas. Donec sem eros, tincidunt at congue ut, posuere sit amet est. Vivamus scelerisque viverra odio sit amet laoreet. Ut nec neque non justo rutrum tempor lobortis eu ante. Aliquam sagittis, nibh quis commodo auctor</p>
  <a href="#" class="btn btn-main">Request Consultant</a>
  <p class="btn-caption">Our web professionals will contact<br>you to discuss your project</p>

  <div class="info-box"><span class="info-icon">i</span>As your full service marketing partner, we will deliver and end to end marketing solution for your business.</div>

  <footer>
    <div class="footer-links">
      <a href="#">Home</a> &nbsp;.&nbsp; <a href="#">About Us</a> &nbsp;.&nbsp; <a href="#">Portfolio</a> &nbsp;.&nbsp; <a href="#">Contact Us</a><br>
      Copyright © 2014 KVR Studios Inc - All Right Reserved<br>
      www.brightpolehub.example
    </div>
    <div class="social footer-social">
      <span aria-label="Social network"></span><span aria-label="Social network"></span>
      <span aria-label="Video channel"></span><span aria-label="Social network"></span>
    </div>
    <div class="phone footer-phone">
      <svg width="14" height="20" viewBox="0 0 14 20"><path d="M3 1 L6 1 L7 6 L5 7.5 Q6.5 12 9 14 L10.5 12.5 L13.5 15 L12 19 Q2 16 1 4 Z" fill="#fff"/></svg>
      1800-555-0142
    </div>
    <a href="#" class="btn btn-footer">Request Consultant</a>
    <div class="footer-bar">
      <div class="partner-badge" role="img" aria-label="Partner badge"></div>
    </div>
  </footer>
</body>
</html>
```